Blockchain Analytics Firm Needs Logo And Website Design

We need a logo and a very basic website for a company based in Linköping, Sweden called 'Vextor'. We build custom machine learning and AI solutions for companies based on blockchain. We are not picky about the colors, but the design should communicate modernity and stability.
We like the following websites:
https://www.pallidwren.co.uk/
https://www.tormacapitalhouse.com/
Target Market(s)
Our customers are startups that have their own product based on blockchain or other distributed ledger technology.
Industry/Entity Type
It Company
Contact Information for Business Card
Name, title and email address
Logo Text
Our company name and "Blockchain Analytics"
Font styles to use
Colors
Designer to choose colors to be used in the design.
Requirements
Must have
- The website and logo need to be modern and clean. In the beginning, we will not be filling out all sections of the website (team, clients, etc.) but we will need to have these set up so we can eventually use them.
Nice to have
- We like angular graphics and some animations on the webpage would be nice.

```html
<!DOCTYPE html>
<html lang="en">
<head>
<meta charset="utf-8">
<title>Vextor Blockchain Analytics</title>
<link href="https://fonts.googleapis.com/css2?family=Lato:wght@400;700;900&family=Open+Sans:ital,wght@0,400;0,600;0,700;1,400&display=swap" rel="stylesheet">
<style>
:root{
  --bg:#1b1b1d;
  --bg-deep:#141416;
  --panel:#222226;
  --white:#ffffff;
  --muted:#d6d6d6;
  --line:#5a5a5e;
  --orange:#f7941d;
  --red:#e53e3e;
  --violet:#5a35d8;
  --blue:#3a8ee6;
}
*{margin:0;padding:0;box-sizing:border-box}
html,body{width:1200px;height:3974px;overflow:hidden;background:var(--bg)}
body{position:relative;font-family:"Open Sans",sans-serif;color:var(--white)}
.abs{position:absolute}
.bg-shapes{position:absolute;left:0;top:0;width:1200px;height:3974px}
.center{left:0;width:1200px;text-align:center}
h1,h2,.brand-name,.blog-title{font-family:"Lato",sans-serif}
.brand{left:100px;top:34px;display:flex;align-items:center;gap:14px}
.brand-mark{width:50px;height:50px;background:var(--orange)}
.brand-name{font-size:38px;font-weight:900;line-height:1;letter-spacing:1px}
.brand-sub{font-size:14px;margin-top:4px;color:var(--white)}
.menu{left:1060px;top:64px;width:40px}
.menu span{display:block;height:4px;background:var(--white);margin-bottom:8px;border-radius:2px}
.menu span:nth-child(2){width:30px;margin-left:10px}
.hero-title{top:178px;font-size:58px;font-weight:700}
.hero-sub{top:262px;font-size:24px;line-height:39px;color:var(--muted)}
.service-label{top:582px;width:240px;text-align:center;font-size:19px;font-weight:600}
h2{font-size:40px;font-weight:900;letter-spacing:.5px}
.intro{left:185px;width:830px;top:930px;font-size:15.5px;line-height:30px;text-align:center;color:var(--muted)}
.video{left:339px;top:1116px;width:522px;height:339px;border:4px solid var(--white);background:linear-gradient(160deg,#2d2733 0%,#1a1719 55%,#3a2a20 100%)}
.play{left:560px;top:1243px;width:84px;height:84px;border-radius:50%;background:#111}
.card{top:1847px;width:308px;height:201px;border:2px solid var(--white);background:var(--bg);text-align:center;padding:70px 22px 0}
.card q{display:block;font-style:italic;font-size:13.5px;line-height:25px;color:var(--muted);quotes:none}
.card .who{margin-top:10px;font-size:18px;font-weight:600;color:var(--white)}
.avatar{top:1804px;width:84px;height:84px;border-radius:50%;border:4px solid var(--white);background:linear-gradient(180deg,#c9b6a5,#7a6a60)}
.arrow-btn{top:1928px;width:40px;height:40px;border-radius:50%;background:#3a3a3e;display:flex;align-items:center;justify-content:center}
.blog-title{top:2764px;width:395px;text-align:center;font-size:24px;font-weight:700}
.blog-date{top:2798px;width:395px;text-align:center;font-size:15px;color:var(--muted)}
.field{height:40px;background:var(--white);color:#666;font-size:13px;padding:10px 16px}
.submit{left:535px;top:3424px;width:130px;height:45px;border-radius:23px;background:var(--orange);font-size:15px;font-weight:700;text-align:center;line-height:45px}
.social{top:3744px;width:48px;height:48px;border-radius:50%;border:2px solid var(--white)}
.foot{font-size:14px;color:var(--muted)}
.vline{width:2px;background:var(--line);left:599px}
.dot{width:30px;height:30px;border-radius:50%;background:var(--orange);left:585px}
</style>
</head>
<body>

<svg class="bg-shapes" viewBox="0 0 1200 3974" aria-hidden="true">
  <defs>
    <linearGradient id="heroGlow" x1="0" y1="0" x2="0" y2="1">
      <stop offset="0" stop-color="#17171a"/>
      <stop offset="0.45" stop-color="#1f2230"/>
      <stop offset="1" stop-color="#1b1b1d"/>
    </linearGradient>
  </defs>
  <rect width="1200" height="3974" fill="var(--bg)"/>
  <rect width="1200" height="900" fill="url(#heroGlow)"/>
  <polygon points="0,640 420,480 1200,580 1200,900 0,900" fill="#1a1a1c" opacity="0.6"/>
  <polygon points="0,1450 700,1300 1200,1560 1200,1700 0,1700" fill="#202023"/>
  <polygon points="0,2150 600,2350 1200,2100 1200,2200 600,2450 0,2250" fill="#19191b"/>
  <polygon points="0,2900 900,2820 1200,3000 1200,3200 0,3100" fill="#1f1f22"/>
  <polygon points="0,3500 500,3600 1200,3450 1200,3974 0,3974" fill="#18181a"/>
</svg>

<header>
  <div class="abs brand">
    <div class="brand-mark"></div>
    <div>
      <div class="brand-name">VEXTOR</div>
      <div class="brand-sub">Blockchain Analytics</div>
    </div>
  </div>
  <div class="abs menu" aria-label="Menu"><span></span><span></span></div>
</header>

<section class="hero">
  <h1 class="abs center hero-title">Vextor Blockchain Analytics</h1>
  <p class="abs center hero-sub">We build custom machine learning and AI solutions<br>for companies based on blockchain</p>

  <svg class="abs" style="left:0;top:390px" width="1200" height="260" viewBox="0 390 1200 260" aria-hidden="true">
    <line x1="366" y1="477" x2="837" y2="477" stroke="var(--line)" stroke-width="2"/>
    <g fill="none" stroke-width="9" stroke-linejoin="round">
      <rect x="313" y="424" width="106" height="106" rx="8" transform="rotate(45 366 477)" stroke="var(--red)"/>
      <rect x="548" y="424" width="106" height="106" rx="8" transform="rotate(45 601 477)" stroke="var(--violet)"/>
      <rect x="784" y="424" width="106" height="106" rx="8" transform="rotate(45 837 477)" stroke="var(--blue)"/>
    </g>
    <g fill="var(--orange)">
      <circle cx="438" cy="477" r="15"/>
      <circle cx="529" cy="477" r="15"/>
      <circle cx="674" cy="477" r="15"/>
      <circle cx="765" cy="477" r="15"/>
    </g>
    <g fill="var(--white)">
      <circle cx="358" cy="483" r="12"/>
      <circle cx="376" cy="466" r="8"/>
    </g>
    <g fill="none" stroke="var(--white)" stroke-width="5" stroke-dasharray="4 4">
      <circle cx="358" cy="483" r="15"/>
      <circle cx="376" cy="466" r="10"/>
    </g>
    <circle cx="358" cy="483" r="4" fill="var(--bg)"/>
    <circle cx="376" cy="466" r="3" fill="var(--bg)"/>
    <g fill="var(--white)">
      <rect x="587" y="478" width="6" height="14"/>
      <rect x="597" y="466" width="6" height="26"/>
      <rect x="607" y="472" width="6" height="20"/>
      <rect x="617" y="460" width="6" height="32"/>
    </g>
    <path d="M580 458 V496 H626" fill="none" stroke="var(--white)" stroke-width="3"/>
    <rect x="820" y="460" width="34" height="34" rx="3" fill="var(--white)"/>
    <g stroke="var(--white)" stroke-width="3">
      <path d="M826 454v6M833 454v6M840 454v6M847 454v6M826 494v6M833 494v6M840 494v6M847 494v6M814 466h6M814 473h6M814 480h6M814 487h6M854 466h6M854 473h6M854 480h6M854 487h6"/>
    </g>
    <text x="837" y="483" text-anchor="middle" font-family="Lato,sans-serif" font-weight="900" font-size="15" fill="var(--bg)">AI</text>
  </svg>
  <div class="abs service-label" style="left:246px">Machine Learning</div>
  <div class="abs service-label" style="left:481px">Data Analytics</div>
  <div class="abs service-label" style="left:717px">AI solutions</div>
</section>

<div class="abs vline" style="top:618px;height:166px"></div>
<div class="abs dot" style="top:783px"></div>

<section class="welcome">
  <h2 class="abs center" style="top:852px">WELCOME TO VEXTOR</h2>
  <p class="abs intro">Vextor is a data analytics startup that can quickly deploy custom machine learning and AI solutions for companies based on Distributed Ledger Technologies (DLT) such as Blockchains. A massive amount of data is generated from these Smart Contracts, particularly from Internet of Things (IoT) applications. We combine this information with traditional data pipelines and present a complete package to our customer.</p>
  <div class="abs video" role="img" aria-label="Video still of a presenter on stage in front of a projected company slide"></div>
  <div class="abs play"></div>
  <svg class="abs" style="left:560px;top:1243px" width="84" height="84" viewBox="0 0 84 84" aria-hidden="true"><polygon points="34,26 60,42 34,58" fill="var(--white)"/></svg>
</section>

<div class="abs vline" style="top:1459px;height:202px"></div>
<div class="abs dot" style="top:1660px"></div>

<section class="testimonials">
  <h2 class="abs center" style="top:1730px">TESTIMONIALS</h2>
  <div class="abs vline" style="top:2050px;height:200px"></div>
  <div class="abs card" style="left:98px">
    <q>Nam libero tempore, cum soluta nobis est eligendi optio cumque nihil impedit quo minus id quod maxime placea</q>
    <div class="who">Tilda Renvall</div>
  </div>
  <div class="abs card" style="left:446px">
    <q>Nam libero tempore, cum soluta nobis est eligendi optio cumque nihil impedit quo minus id quod maxime placea</q>
    <div class="who">Marit Oxelgren</div>
  </div>
  <div class="abs card" style="left:795px">
    <q>Nam libero tempore, cum soluta nobis est eligendi optio cumque nihil impedit quo minus id quod maxime placea</q>
    <div class="who">Petrus Alming</div>
  </div>
  <div class="abs avatar" style="left:210px" role="img" aria-label="Portrait of a client"></div>
  <div class="abs avatar" style="left:558px" role="img" aria-label="Portrait of a client"></div>
  <div class="abs avatar" style="left:907px" role="img" aria-label="Portrait of a client"></div>
  <div class="abs arrow-btn" style="left:28px"><svg width="14" height="14" viewBox="0 0 14 14" aria-hidden="true"><path d="M9 2 4 7l5 5" fill="none" stroke="var(--white)" stroke-width="2.5"/></svg></div>
  <div class="abs arrow-btn" style="left:1130px"><svg width="14" height="14" viewBox="0 0 14 14" aria-hidden="true"><path d="M5 2l5 5-5 5" fill="none" stroke="var(--white)" stroke-width="2.5"/></svg></div>
</section>

<div class="abs dot" style="top:2251px"></div>

<section class="blog">
  <h2 class="abs center" style="top:2333px">LATEST BLOG</h2>
  <div class="abs" style="left:98px;top:2457px;width:305px;height:278px;background:linear-gradient(135deg,#f0655a,#d8302f)" role="img" aria-label="Hands holding a glowing globe of network icons"></div>
  <div class="abs" style="left:798px;top:2457px;width:304px;height:278px;background:linear-gradient(135deg,#b7a6ef,#7a4ae0)" role="img" aria-label="People working on laptops with charts"></div>
  <div class="abs" style="left:403px;top:2433px;width:395px;height:326px;background:linear-gradient(160deg,#3fa6ec,#1f6fcf)" role="img" aria-label="Digital brain made of connected network points"></div>
  <div class="abs blog-title" style="left:53px">Finibus Bonoedrt Mal</div>
  <div class="abs blog-title" style="left:403px">Finibus Bonoedrt Mal</div>
  <div class="abs blog-title" style="left:738px">Finibus Bonoedrt Mal</div>
  <div class="abs blog-date" style="left:53px">&#9638; 15/06/218</div>
  <div class="abs blog-date" style="left:403px">&#9638; 15/06/218</div>
  <div class="abs blog-date" style="left:738px">&#9638; 15/06/218</div>
</section>

<div class="abs vline" style="top:2830px;height:216px"></div>
<div class="abs dot" style="top:3046px"></div>

<section class="contact">
  <h2 class="abs center" style="top:3112px">CONTACT US</h2>
  <div class="abs field" style="left:260px;top:3196px;width:334px">First Name</div>
  <div class="abs field" style="left:607px;top:3196px;width:334px">Last Name</div>
  <div class="abs field" style="left:260px;top:3252px;width:334px">Email Address</div>
  <div class="abs field" style="left:607px;top:3252px;width:334px">Phone Number</div>
  <div class="abs field" style="left:260px;top:3305px;width:681px;height:82px">Message</div>
  <div class="abs submit">SUBMIT</div>
</section>

<div class="abs vline" style="top:3470px;height:205px"></div>
<div class="abs dot" style="top:3674px"></div>

<footer>
  <div class="abs social" style="left:487px" aria-label="Social link"></div>
  <div class="abs social" style="left:546px" aria-label="Social link"></div>
  <div class="abs social" style="left:604px" aria-label="Social link"></div>
  <div class="abs social" style="left:662px" aria-label="Social link"></div>
  <div class="abs center foot" style="top:3829px">
    <svg width="12" height="14" viewBox="0 0 12 14" aria-hidden="true"><path d="M6 0a5 5 0 0 0-5 5c0 4 5 9 5 9s5-5 5-9a5 5 0 0 0-5-5z" fill="var(--white)"/><circle cx="6" cy="5" r="2" fill="var(--bg)"/></svg>
    Halvik Science Park, Granbacken 9, SE-583 41 Linköping, SWEDEN &nbsp; | &nbsp;
    <svg width="13" height="13" viewBox="0 0 13 13" aria-hidden="true"><path d="M3 0l2 3-1.5 1.5a8 8 0 0 0 5 5L10 8l3 2-1.5 2.5C6 13 0 7 .5 1.5z" fill="var(--white)"/></svg>
    1 555 010 2040 &nbsp; | &nbsp;
    <svg width="15" height="11" viewBox="0 0 15 11" aria-hidden="true"><rect width="15" height="11" fill="var(--white)"/><path d="M0 0l7.5 6L15 0" fill="none" stroke="var(--bg)" stroke-width="1.5"/></svg>
    hello@vextor.com
  </div>
  <div class="abs center foot" style="top:3870px">Help &nbsp;|&nbsp; FAQ &nbsp;|&nbsp; Support &nbsp;|&nbsp; Sitemap &nbsp;|&nbsp; Terms Of Use &nbsp;|&nbsp; Privacy Statement</div>
  <div class="abs center foot" style="top:3907px">Copyrights © 2018, Vextor. All rights reserved.</div>
</footer>

</body>
</html>
```